Global (re)insurance broker needs a business card design

We need a classic business card for our company that is headquartered in SG, with offices in Malaysia and Dubai. We specialise in insurance and reinsurance broking and consultancy for our global clients.

```html
<!DOCTYPE html>
<html lang="en">
<head>
<meta charset="utf-8">
<title>Norvale Business Card</title>
<link href="https://fonts.googleapis.com/css2?family=Open+Sans:wght@300;400;700;800&display=swap" rel="stylesheet">
<style>
  :root {
    --canvas: #2b2b2f;
    --card: #151515;
    --blue: #2a4b9e;
    --mint: #c5dfbb;
    --ink: #f2f2f2;
  }
  * { box-sizing: border-box; margin: 0; padding: 0; }
  html, body { width: 1200px; height: 947px; overflow: hidden; }
  body {
    background: var(--canvas);
    font-family: "Open Sans", Arial, sans-serif;
    display: flex;
    flex-direction: column;
    align-items: center;
    justify-content: center;
    gap: 52px;
  }
  .card {
    position: relative;
    width: 700px;
    height: 400px;
    background: var(--card);
    border-radius: 22px;
    overflow: hidden;
  }
  .card-front { display: flex; align-items: center; justify-content: center; }
  .wordmark {
    font-weight: 800;
    color: var(--mint);
    letter-spacing: 4px;
    line-height: 1;
  }
  .card-front .wordmark { font-size: 104px; }
  .card-back .wordmark {
    position: absolute;
    left: 48px;
    top: 176px;
    font-size: 50px;
    letter-spacing: 2px;
  }
  .divider {
    position: absolute;
    left: 338px;
    top: 62px;
    width: 2px;
    height: 250px;
    background: var(--mint);
  }
  .details {
    position: absolute;
    left: 366px;
    top: 58px;
    color: var(--ink);
  }
  .person-name { font-size: 25px; font-weight: 800; line-height: 1.1; }
  .person-name .first { color: var(--blue); }
  .person-name .last { color: var(--mint); }
  .person-title { font-size: 17px; font-weight: 300; margin-top: 4px; }
  .contact-list { list-style: none; margin-top: 18px; font-size: 15px; font-weight: 400; }
  .contact-list li { display: flex; align-items: center; gap: 8px; line-height: 1.55; }
  .contact-list svg { width: 12px; height: 12px; fill: var(--ink); flex: none; }
  .address { margin-top: 16px; font-size: 15px; font-weight: 400; line-height: 1.5; }
  .edge-band { position: absolute; left: 0; bottom: 0; width: 700px; height: 30px; }
</style>
</head>
<body>
  <section class="card card-front">
    <div class="wordmark">NORVALE</div>
  </section>

  <section class="card card-back">
    <div class="wordmark">NORVALE</div>
    <div class="divider"></div>
    <div class="details">
      <p class="person-name"><span class="first">Mira</span> <span class="last">Lindqvist</span></p>
      <p class="person-title">Chief Operating Officer</p>
      <ul class="contact-list">
        <li><svg viewBox="0 0 24 24"><path d="M6.6 10.8a15 15 0 0 0 6.6 6.6l2.2-2.2c.3-.3.7-.4 1-.2 1.1.4 2.3.6 3.6.6.6 0 1 .4 1 1V20c0 .6-.4 1-1 1A17 17 0 0 1 3 4c0-.6.4-1 1-1h3.5c.6 0 1 .4 1 1 0 1.3.2 2.5.6 3.6.1.3 0 .7-.2 1z"/></svg>+65 9123 4567</li>
        <li><svg viewBox="0 0 24 24"><path d="M2 5h20v14H2z M2 5l10 8 10-8" fill="none" stroke="#f2f2f2" stroke-width="2"/></svg>mira@norvale.com</li>
        <li><svg viewBox="0 0 24 24"><circle cx="12" cy="12" r="10" fill="none" stroke="#f2f2f2" stroke-width="2"/><path d="M2 12h20M12 2c3 3 3 17 0 20M12 2c-3 3-3 17 0 20" fill="none" stroke="#f2f2f2" stroke-width="1.6"/></svg>www.norvale.com</li>
      </ul>
      <p class="address">28 Harbour Lane,<br>Meridian Tower #12-04,<br>Singapore 018925</p>
    </div>
    <svg class="edge-band" viewBox="0 0 700 30" aria-hidden="true">
      <polygon points="0,30 0,12 470,12 448,30" fill="var(--blue)"/>
      <polygon points="462,12 700,0 700,30 440,30" fill="var(--mint)"/>
      <polygon points="0,30 0,12 470,12 448,30" fill="var(--blue)"/>
    </svg>
  </section>
</body>
</html>
```